Largest women's organization in New Hampshire needs a new graphic for their Facebook, Twitter and LI

Our organization is celebrating its 10th anniversary and we are the largest organization in New Hampshire for personal and professional development, businesses resources, networking and fun. Our "vibe" is one of community, fun, polished professionalism, feminity and lots of motivation and inspiration. We like quotes like "she believed she could so she did" and "stimulate your mind, nurture your soul" which is kind of our tag line. Our colors are pink, black, white and lime green. We host a lot of events with the biggest being the NH Larkridge Summit Days. Our website is www.larkridgeforum.com / https://www.frendlio.com/LarkridgeCircleForum/?ref=bookmarks

```html
<!DOCTYPE html>
<html lang="en">
<head>
<meta charset="utf-8">
<title>Larkridge Circle Forum – She Believed She Could So She Did</title>
<link href="https://fonts.googleapis.com/css2?family=Great+Vibes&family=Open+Sans:ital,wght@1,400&family=Montserrat:wght@600;700&display=swap" rel="stylesheet">
<style>
  :root {
    --slate: #2b3132;
    --ink: #141717;
    --pink: #e2559e;
    --purple: #7d3ea3;
    --photo-light: #eea3c9;
    --photo-mid: #e07cb0;
    --photo-deep: #c95a95;
    --white: #ffffff;
    --logo-ink: #1c1c1c;
  }
  * { margin: 0; padding: 0; box-sizing: border-box; }
  html, body { width: 1200px; height: 457px; overflow: hidden; background: var(--slate); }
  .banner { position: relative; width: 1200px; height: 457px; overflow: hidden; background: var(--slate); }
  .banner__shapes { position: absolute; inset: 0; }
  .brand {
    position: absolute; left: 52px; top: 268px;
    display: flex; align-items: center; gap: 12px;
    font-family: "Montserrat", sans-serif; font-weight: 700;
    font-size: 25px; line-height: 1.1; color: var(--logo-ink);
  }
  .brand__dot { width: 22px; height: 22px; border-radius: 50%; background: var(--logo-ink); flex: none; }
  .quote { position: absolute; inset: 0; font-weight: 400; }
  .quote__line { position: absolute; white-space: nowrap; line-height: 1; }
  .quote__she {
    left: 850px; top: 40px;
    font-family: "Great Vibes", cursive; font-size: 84px; color: var(--purple);
  }
  .quote__believed {
    left: 728px; top: 86px;
    font-family: "Great Vibes", cursive; font-size: 108px; color: var(--pink);
  }
  .quote__could {
    left: 690px; top: 184px;
    font-family: "Open Sans", sans-serif; font-style: italic; font-weight: 400;
    font-size: 29px; letter-spacing: -0.3px; color: var(--purple);
  }
  .quote__did {
    left: 858px; top: 204px;
    font-family: "Great Vibes", cursive; font-size: 100px; color: var(--pink);
  }
  .tagline {
    position: absolute; left: 753px; top: 340px; width: 290px;
    font-family: "Montserrat", sans-serif; font-weight: 600;
    font-size: 22px; line-height: 29px; text-align: center; color: var(--white);
  }
</style>
</head>
<body>
<main class="banner">
  <svg class="banner__shapes" width="1200" height="457" viewBox="0 0 1200 457">
    <defs>
      <linearGradient id="photoTint" x1="0" y1="0" x2="1" y2="1">
        <stop offset="0" stop-color="var(--photo-light)"/>
        <stop offset="0.55" stop-color="var(--photo-mid)"/>
        <stop offset="1" stop-color="var(--photo-deep)"/>
      </linearGradient>
    </defs>
    <rect class="event-photo" x="0" y="0" width="634" height="457" fill="url(#photoTint)" role="img" aria-label="Pink-tinted photo of smiling women seated at a banquet table at the summit"/>
    <polygon class="corner-band" points="634,130 634,457 820,457" fill="var(--ink)"/>
  </svg>

  <div class="brand">
    <span class="brand__dot"></span>
    <span class="brand__name">Larkridge<br>Circle Forum</span>
  </div>

  <h1 class="quote">
    <span class="quote__line quote__she">She</span>
    <span class="quote__line quote__believed">believed</span>
    <span class="quote__line quote__could">she could so</span>
    <span class="quote__line quote__did">she Did</span>
  </h1>

  <p class="tagline">Stimulate Your Mind,<br>Nurture Your Soul</p>
</main>
</body>
</html>
```